American cannabis tech company business card design

Pavrel.com is seeking a modern, professional, and brand-aligned business card that represents our company and its core values: Mission, Story, Values, and Impact. As an innovative cannabis company, we want a business card that is not only visually appealing but also serves as a representation of who we are and what we stand for.

Project Scope: Design a double-sided business card that integrates our brand identity and core values. Incorporate our key brand elements, ensuring a sleek and contemporary aesthetic. Visually reflect our core values (Mission, Story, Values, Impact) in a way that is engaging yet professional.

Target Market(s)

Vendors, third parties,

Contact Information for Business Card

Contact details (name, title, email, phone, website, etc.)

Font styles to use
Other font styles liked:
• Caslon, Centra

Colors

Designer to choose colors to be used in the design.

Requirements
Must have
• Pavrel.com logo and branding A creative yet clean way to integrate our core values (Mission, Story, Values, Impact) Modern typography and a well-structured layout
Nice to have
• forest green, grey, white, black
Should not have
• references to marijuana, leafs, plants, or related product

```html
<!DOCTYPE html>
<html lang="en">
<head>
<meta charset="utf-8">
<title>Pavrel.com Business Card</title>
<link rel="stylesheet" href="https://fonts.googleapis.com/css2?family=Libre+Caslon+Text:wght@400;700&display=swap">
<style>
  :root {
    --forest: #1a3a1f;
    --cream: #fbf8f1;
    --paper: #ffffff;
    --ink: #1c1c1c;
    --backdrop: #3a3a3a;
  }
  html, body {
    margin: 0;
    padding: 0;
    width: 1200px;
    height: 689px;
    overflow: hidden;
    background: var(--backdrop);
  }
  .sheet {
    position: relative;
    width: 1200px;
    height: 689px;
    display: flex;
    align-items: center;
    justify-content: center;
    gap: 48px;
    font-family: "Libre Caslon Text", Georgia, serif;
  }
  .card {
    position: relative;
    width: 520px;
    height: 297px;
    border-radius: 22px;
    box-sizing: border-box;
  }
  .card--front {
    background: var(--forest);
    display: flex;
    align-items: center;
    justify-content: center;
  }
  .wordmark {
    margin: 0;
    font-weight: 700;
    letter-spacing: 1px;
    line-height: 1;
  }
  .card--front .wordmark {
    color: var(--cream);
    font-size: 84px;
  }
  .card--back {
    background: var(--paper);
    color: var(--forest);
    padding: 28px 34px 20px;
  }
  .card--back .wordmark {
    color: var(--forest);
    font-size: 62px;
    text-align: center;
  }
  .details {
    display: flex;
    align-items: center;
    justify-content: center;
    margin-top: 22px;
    gap: 18px;
  }
  .person {
    text-align: right;
  }
  .person__name {
    margin: 0;
    font-size: 19px;
    font-weight: 700;
    color: var(--forest);
  }
  .person__role {
    margin: 2px 0 0;
    font-size: 12px;
    color: var(--ink);
  }
  .divider {
    width: 1px;
    height: 64px;
    background: var(--forest);
  }
  .contact {
    list-style: none;
    margin: 0;
    padding: 0;
    font-size: 12.5px;
    color: var(--ink);
  }
  .contact li {
    display: flex;
    align-items: center;
    gap: 8px;
    line-height: 21px;
  }
  .contact svg {
    width: 13px;
    height: 13px;
    fill: var(--forest);
    flex: none;
  }
  .address {
    margin-top: 14px;
    text-align: center;
    font-size: 12.5px;
    color: var(--ink);
  }
  .address svg {
    display: block;
    margin: 0 auto 5px;
    width: 20px;
    height: 20px;
  }
  .values {
    list-style: none;
    margin: 12px 0 0;
    padding: 0;
    display: flex;
    justify-content: center;
    gap: 14px;
    font-size: 10px;
    letter-spacing: 2px;
    text-transform: uppercase;
    color: var(--forest);
  }
  .values li + li::before {
    content: "";
    display: inline-block;
    width: 4px;
    height: 4px;
    margin: 0 14px 2px 0;
    background: var(--forest);
    border-radius: 50%;
  }
</style>
</head>
<body>
<main class="sheet">
  <section class="card card--front" aria-label="Card front">
    <h1 class="wordmark">PAVREL</h1>
  </section>

  <section class="card card--back" aria-label="Card back">
    <h2 class="wordmark">PAVREL</h2>
    <div class="details">
      <div class="person">
        <p class="person__name">Daniel Rowe</p>
        <p class="person__role">Owner</p>
      </div>
      <span class="divider"></span>
      <ul class="contact">
        <li>
          <svg viewBox="0 0 24 24" aria-hidden="true"><path d="M6.6 10.8a15 15 0 0 0 6.6 6.6l2.2-2.2c.3-.3.7-.4 1-.2 1.1.4 2.3.6 3.6.6.6 0 1 .4 1 1V20c0 .6-.4 1-1 1A17 17 0 0 1 3 4c0-.6.4-1 1-1h3.5c.6 0 1 .4 1 1 0 1.3.2 2.5.6 3.6.1.3 0 .7-.2 1z"/></svg>
          044-987 654 321
        </li>
        <li>
          <svg viewBox="0 0 24 24" aria-hidden="true"><path d="M2 5h20v14H2zM4 7v.4l8 5 8-5V7l-8 5z"/></svg>
          hello@pavrel.com
        </li>
        <li>
          <svg viewBox="0 0 24 24" aria-hidden="true"><path d="M12 2a10 10 0 1 0 0 20 10 10 0 0 0 0-20zm6.9 6h-3a15 15 0 0 0-1.3-3.9A8 8 0 0 1 18.9 8zM12 4c.8 1.2 1.5 2.5 1.9 4h-3.8c.4-1.5 1.1-2.8 1.9-4zM4.3 14a8 8 0 0 1 0-4h3.4a16 16 0 0 0 0 4zm.8 2h3a15 15 0 0 0 1.3 3.9A8 8 0 0 1 5.1 16zm3-8h-3a8 8 0 0 1 4.3-3.9A15 15 0 0 0 8.1 8zM12 20c-.8-1.2-1.5-2.5-1.9-4h3.8c-.4 1.5-1.1 2.8-1.9 4zm2.3-6H9.7a14 14 0 0 1 0-4h4.6a14 14 0 0 1 0 4zm.3 5.9a15 15 0 0 0 1.3-3.9h3a8 8 0 0 1-4.3 3.9zm1.7-5.9a16 16 0 0 0 0-4h3.4a8 8 0 0 1 0 4z"/></svg>
          www.pavrel.com
        </li>
      </ul>
    </div>
    <div class="address">
      <svg viewBox="0 0 24 24" aria-hidden="true">
        <circle cx="12" cy="12" r="11" fill="none" stroke="#1a3a1f" stroke-width="1.5"/>
        <path d="M12 5.5a4 4 0 0 0-4 4c0 3 4 8 4 8s4-5 4-8a4 4 0 0 0-4-4zm0 5.5a1.5 1.5 0 1 1 0-3 1.5 1.5 0 0 1 0 3z" fill="#1a3a1f"/>
      </svg>
      218 Cedar Row, Suite 40, Denver 80205, USA
    </div>
    <ul class="values" aria-label="Core values">
      <li>Mission</li>
      <li>Story</li>
      <li>Values</li>
      <li>Impact</li>
    </ul>
  </section>
</main>
</body>
</html>
```